kolvarin.link kolvarin.space kolvarin.press website

The website is named KOLVARIN and it will have 3 domain names. kolvarin.link, press, space.
I'd like it to be viewed on Pads, pcs and phones.

page menu:

kolvarin.link(start page): presentation of company. (creative, design, app, new product innovation.)
Here we'll need sosial media icons: plimber, vendoloop, mirtavel, trelvanet. (light but some 'fruity' colors)

kolvarin.press: blog. It will be a 75% picture blog > rest will be text. I need to be able to resize pictures and shape columns to picture size. (light but some 'fruity' colors)

kolvarin.space : the fun part of this web design, however, on entering the page I'd like a non-disclosure agreement where viewer simply click "yes, I agree" after filling out contact info. (check attached document)
We will have space here for uploading PDF files viewers can download. There is also a blog space here to tell in brief about the PDF file. (maybe a space/sci-fi theme her e.g spacechimp, Laika the space dog?)

I will attach the logo here I want you to use > and develop for the .space .press webpage. The logo i uploaded is for the .link page.

Target Market(s)

venture capitalists

Number of Pages Required

3 page

Requirements
Must have
• a few 'fruity colors' but mostly white and grey

```html
<!DOCTYPE html>
<html lang="en">
<head>
<meta charset="utf-8">
<title>KOLVARIN LINK</title>
<link rel="stylesheet" href="https://fonts.googleapis.com/css2?family=Lato:wght@400;700;900&family=Raleway:wght@300;400;700&display=swap">
<style>
:root{
  --white:#ffffff;
  --paper:#f5f5f5;
  --ink:#2b2b2b;
  --grey:#666a6e;
  --line:#bfc2c5;
  --leaf:#6aa84f;
  --orange:#f26a1b;
  --gold:#f5a623;
  --green-card:#5e9a3c;
  --red-card:#e04a2e;
  --yellow-card:#f6ab16;
  --band:#3d3e42;
  --footer:#3a3b3f;
  --base:#1f1f21;
}
*{margin:0;padding:0;box-sizing:border-box}
html,body{width:830px;height:1200px;overflow:hidden;background:var(--white)}
body{position:relative;font-family:'Lato',sans-serif;color:var(--ink)}
.abs{position:absolute}

/* header */
.site-header{left:0;top:0;width:830px;height:86px;background:var(--white)}
.brand-tab{left:66px;top:0;width:148px;height:108px;background:var(--white);box-shadow:0 3px 5px rgba(0,0,0,.18);z-index:3;display:flex;flex-direction:column;align-items:center;justify-content:center;gap:6px}
.brand-mark{width:22px;height:22px;background:var(--leaf)}
.brand-name{font-weight:900;font-size:20px;color:var(--ink);letter-spacing:.5px;text-align:center;line-height:1.05}
.contact-item{display:flex;align-items:center;gap:10px;top:34px}
.contact-item .label{font-size:10px;color:var(--leaf);font-weight:700;line-height:1.2}
.contact-item .value{font-size:10.5px;color:var(--grey);line-height:1.3}

/* hero */
.hero{left:0;top:86px;width:830px;height:383px;
  background:
    radial-gradient(ellipse 90px 60px at 455px 95px,rgba(240,232,200,.55),transparent 70%),
    radial-gradient(ellipse 150px 120px at 210px 200px,rgba(214,170,140,.55),transparent 72%),
    radial-gradient(ellipse 190px 150px at 470px 210px,rgba(170,60,190,.75),rgba(90,60,170,.35) 55%,transparent 80%),
    radial-gradient(ellipse 120px 80px at 540px 250px,rgba(60,170,120,.45),transparent 75%),
    radial-gradient(ellipse 110px 70px at 390px 260px,rgba(230,60,70,.5),transparent 75%),
    radial-gradient(ellipse 300px 45px at 440px 320px,rgba(60,110,210,.6),transparent 75%),
    linear-gradient(90deg,#2a2a2d 0%,#3c3c40 25%,#2a2a2e 55%,#202023 80%,#151517 100%)}
.hero-caption{left:0;top:324px;width:830px;height:59px;background:rgba(20,20,22,.75);display:flex;align-items:center;justify-content:center;font-family:'Raleway',sans-serif;font-weight:700;font-size:21px;color:var(--white)}
.hero-arrow{top:176px}

/* about */
.about{left:0;top:469px;width:830px;height:395px;background:var(--paper)}
.about-title{left:0;top:30px;width:830px;text-align:center;font-family:'Raleway',sans-serif;font-weight:700;font-size:17px;color:var(--ink)}
.about-title span{color:var(--orange)}
.about-rule{left:273px;top:66px;width:284px;height:1px;background:var(--line)}
.about-rule-dot{left:409px;top:60px;width:12px;height:12px;background:var(--red-card);border:2px solid var(--green-card);border-radius:2px}
.about-text{left:62px;top:96px;width:706px;text-align:center;font-size:8.5px;line-height:16.5px;color:var(--ink)}

.services-band{left:0;top:757px;width:830px;height:107px;background:var(--band)}
.service{top:668px;width:190px;height:196px}
.service-face{left:0;top:0;width:167px;height:154px;overflow:hidden}
.service-side{left:167px;top:0;width:23px;height:196px;background:linear-gradient(180deg,#b3b3b3,#8e8e8e);clip-path:polygon(0 0,100% 14%,100% 100%,0 100%)}
.service-label{left:0;top:154px;width:167px;height:42px;background:linear-gradient(180deg,#2a2b2e,#46474b);display:flex;align-items:center;justify-content:center;font-weight:900;font-size:13px;color:var(--white)}
.service svg{position:absolute;left:0;top:0}

/* consultation */
.consult{left:61px;top:891px;width:708px;height:181px;background:linear-gradient(120deg,#6c7076 0%,#555a60 45%,#70757b 100%)}
.consult-title{left:0;top:34px;width:708px;text-align:center;font-family:'Raleway',sans-serif;font-weight:400;font-size:26px;color:var(--white)}
.consult-sub{left:0;top:78px;width:708px;text-align:center;font-family:'Raleway',sans-serif;font-weight:400;font-size:17px;line-height:22px;color:var(--white)}
.consult-phone{left:0;top:130px;width:708px;display:flex;justify-content:center;align-items:center;gap:8px;font-family:'Raleway',sans-serif;font-size:23px;color:var(--gold)}
.consult-dots{right:24px;bottom:11px;display:flex;gap:5px}
.consult-dots i{width:7px;height:7px;border-radius:50%;background:var(--white)}
.consult-dots i:first-child{background:var(--gold)}

/* footer */
.site-footer{left:0;top:1098px;width:830px;height:72px;background:var(--footer);color:var(--white)}
.foot-item{top:24px;display:flex;align-items:center;gap:9px}
.foot-item .label{font-size:9.5px;font-weight:700;line-height:1.3}
.foot-item .value{font-size:10.5px;line-height:1.3}
.foot-item .small{font-size:8px;font-weight:700}
.social{left:567px;top:20px;display:flex;align-items:center;gap:8px;font-size:10.5px}
.social-list{display:grid;grid-template-columns:repeat(2,auto);column-gap:10px;row-gap:5px}
.social-list span{display:flex;align-items:center;gap:4px;font-size:9px;line-height:12px;white-space:nowrap}
.social-list span::before{content:"";width:10px;height:10px;border-radius:50%;background:var(--c)}
.site-base{left:0;top:1170px;width:830px;height:30px;background:var(--base);color:#ddd;font-size:9px;display:flex;align-items:center;justify-content:center}
</style>
</head>
<body>

<header class="abs site-header">
  <div class="abs brand-tab">
    <div class="brand-mark"></div>
    <div class="brand-name">KOLVARIN<br>LINK</div>
  </div>
  <div class="abs contact-item" style="left:520px">
    <svg width="22" height="22" viewBox="0 0 22 22" fill="none" stroke="#6aa84f" stroke-width="1.4"><rect x="2" y="8" width="18" height="12"/><path d="M2 8l9 7 9-7"/><path d="M5 9V2h12v7"/><path d="M8 5h6M8 8h6"/></svg>
    <div><div class="label">Mail Us :</div><div class="value">info@kolvarinlink.com</div></div>
  </div>
  <div class="abs contact-item" style="left:677px">
    <svg width="20" height="20" viewBox="0 0 20 20" fill="none" stroke="#6aa84f" stroke-width="1.4"><path d="M4 2l3 3-2 3c1 3 3 5 6 6l3-2 3 3-2 3C8 18 2 12 2 4z"/></svg>
    <div><div class="label">Call Us :</div><div class="value">123-555-0190</div></div>
  </div>
</header>

<section class="abs hero" role="img" aria-label="Photo of a hand touching a tablet with glowing technology icons rising from the screen">
  <svg class="abs hero-arrow" style="left:56px" width="20" height="30" viewBox="0 0 20 30" fill="none" stroke="#fff" stroke-width="2"><path d="M15 2L4 15l11 13"/></svg>
  <svg class="abs hero-arrow" style="left:754px" width="20" height="30" viewBox="0 0 20 30" fill="none" stroke="#fff" stroke-width="2"><path d="M5 2l11 13L5 28"/></svg>
  <div class="abs hero-caption">WE DESIGN &amp; DEVELOP YOUR DREAMS</div>
</section>

<section class="abs about">
  <h2 class="abs about-title">ABOUT <span>KOLVARIN LINK</span></h2>
  <div class="abs about-rule"></div>
  <div class="abs about-rule-dot"></div>
  <p class="abs about-text">Lorem ipsum dolor sit amet, consectetuer adipiscing elit, sed diam nonummy nibh euismod tincidunt ut laoreet dolore magna aliquam erat volutpat. Ut wisi enim ad minim veniam, quis nostrud exerci tation ullamcorper suscipit lobortis nisl ut aliquip ex ea commodo consequat. Duis autem vel eum iriure dolor in hendrerit in vulputate velit esse molestie consequat, vel illum dolore eu feugiat nulla facilisis at vero eros et accumsan et iusto oexerci tation ullamcorper suscipit lobortis nisl ut aliquip ex ea commodo consequat. Duis autem vel eum iriure dolor in hendrerit in vulputate velit esse molestie</p>
</section>

<div class="abs services-band"></div>

<article class="abs service" style="left:110px">
  <div class="abs service-side"></div>
  <div class="abs service-face" style="background:var(--green-card)">
    <svg width="167" height="154" viewBox="0 0 167 154">
      <path d="M124 40L167 83V154H110L58 102z" fill="#416b2a"/>
      <rect x="45" y="40" width="72" height="70" rx="6" fill="#fff"/>
      <rect x="53" y="54" width="56" height="48" fill="#416b2a"/>
      <circle cx="55" cy="47" r="2.5" fill="#416b2a"/><circle cx="62" cy="47" r="2.5" fill="#416b2a"/><circle cx="69" cy="47" r="2.5" fill="#416b2a"/>
      <path d="M66 66l23 23" stroke="#fff" stroke-width="4" stroke-linecap="round"/>
    </svg>
  </div>
  <div class="abs service-label">CREATIVE DESIGN</div>
</article>

<article class="abs service" style="left:332px">
  <div class="abs service-side"></div>
  <div class="abs service-face" style="background:var(--red-card)">
    <svg width="167" height="154" viewBox="0 0 167 154">
      <path d="M100 36L167 100V154H120L60 96z" fill="#8a2617"/>
      <rect x="52" y="36" width="44" height="80" rx="7" fill="#fff"/>
      <circle cx="74" cy="107" r="4" fill="#e04a2e"/>
      <rect x="58" y="52" width="7" height="7" fill="#e04a2e"/><rect x="58" y="65" width="7" height="7" fill="#e04a2e"/><rect x="58" y="78" width="7" height="7" fill="#e04a2e"/>
      <circle cx="97" cy="74" r="16" fill="#fff" stroke="#fff" stroke-width="8" stroke-dasharray="6 4"/>
      <circle cx="97" cy="74" r="6" fill="#e04a2e"/>
    </svg>
  </div>
  <div class="abs service-label">APP DEVELOPMENT</div>
</article>

<article class="abs service" style="left:553px">
  <div class="abs service-side"></div>
  <div class="abs service-face" style="background:var(--yellow-card)">
    <svg width="167" height="154" viewBox="0 0 167 154">
      <path d="M105 48L167 108V154H120L70 106z" fill="#845307"/>
      <path d="M78 41c16 0 27 11 27 25l5 12h-6v10c0 4-3 7-7 7h-7v10H66V93c-7-5-12-13-12-25 0-15 11-27 24-27z" fill="#fff"/>
      <path d="M78 56a9 9 0 0 0-5 16v6h10v-6a9 9 0 0 0-5-16z" fill="none" stroke="#f6ab16" stroke-width="2.5"/>
      <path d="M78 34v-6M64 38l-3-4M92 38l3-4" stroke="#fff" stroke-width="2.5" stroke-linecap="round"/>
    </svg>
  </div>
  <div class="abs service-label">PRODUCT INNOVATION</div>
</article>

<section class="abs consult" role="img" aria-label="Desk seen from above with laptops, notebooks, coffee and printed charts">
  <h2 class="abs consult-title">FREE CONSULTATION</h2>
  <p class="abs consult-sub">Get Free Consultation Call Us Today For<br>An Appointment</p>
  <div class="abs consult-phone">
    <svg width="28" height="28" viewBox="0 0 28 28" fill="none" stroke="#f5a623" stroke-width="2"><circle cx="14" cy="14" r="12.5"/><path d="M10 8l2.5 2.5-1.5 2.5c.8 2 2 3.2 4 4l2.5-1.5L20 18l-2 2c-5 0-10-5-10-10z" fill="#f5a623" stroke="none"/></svg>
    <span>1234 555 019</span>
  </div>
  <div class="abs consult-dots"><i></i><i></i><i></i><i></i></div>
</section>

<footer class="abs site-footer">
  <div class="abs foot-item" style="left:60px">
    <svg width="18" height="24" viewBox="0 0 18 24" fill="none" stroke="#fff" stroke-width="1.4"><path d="M9 23S2 14 2 9a7 7 0 0 1 14 0c0 5-7 14-7 14z"/><circle cx="9" cy="9" r="2.5"/></svg>
    <div><div class="label">KOLVARIN LINK</div><div class="small">lorem ipsum is the dummy</div></div>
  </div>
  <div class="abs foot-item" style="left:243px">
    <svg width="22" height="22" viewBox="0 0 22 22" fill="none" stroke="#fff" stroke-width="1.4"><rect x="2" y="8" width="18" height="12"/><path d="M2 8l9 7 9-7"/><path d="M5 9V2h12v7"/><path d="M8 5h6M8 8h6"/></svg>
    <div><div class="label">Mail Us :</div><div class="value">info@kolvarinlink.com</div></div>
  </div>
  <div class="abs foot-item" style="left:425px">
    <svg width="20" height="20" viewBox="0 0 20 20" fill="none" stroke="#fff" stroke-width="1.4"><path d="M4 2l3 3-2 3c1 3 3 5 6 6l3-2 3 3-2 3C8 18 2 12 2 4z"/></svg>
    <div><div class="label">Call Us :</div><div class="value">123-555-0190</div></div>
  </div>
  <div class="abs social">
    <span>Connect With Us</span>
    <div class="social-list">
      <span style="--c:#2a6db5">mirtavel</span>
      <span style="--c:#1fb3e0">plimber</span>
      <span style="--c:#e2483a">vendoloop</span>
      <span style="--c:#1586c6">trelvanet</span>
    </div>
  </div>
</footer>
<div class="abs site-base">Copyright © 2016 KOLVARIN LINK. All Rights Reserved.</div>

</body>
</html>
```